Webdesign for large cottage directory

We have developed a first version of a website that can accommodate large groups (10 to 300 people). The site is English and is aimed at a wide audience ranging from a group of students to a family or a family. For the visitors the site is free and it is the propietaires who pay to see their accommodation. The site is online with just a few fake lodgings and a simple design to the elements that must be appraised (nothing to keep the current design). Our website is here: 9lodgia.com (login / pass = admin / 123) Home page (9lodgia.com): on this page section) and lodging by theme (third section). These three points should be highlighted as possible. The displayed map may be slightly modified. Only the background and the color changes when hovering over the mouse. It can be enlarged / retreciated. Below these 3 sections we have some fairly published articles, the latest blog posts and the footer. The menu will be visible throughout the site. Category page (https://9lodgia.fr/gite-departement/aveyron OR https://9lodgia.fr/gites-couchages-121): On these pages we always return the same format with the googlemap, an image 1 text. Below the list of the cottages concerned and the filter options. Product page: The pages presenting the cottages can be of two types: - Either the cottage has no owner and there is no contact for the visitor to the owner that he can retrieve his cottage by registering: example of a page of this type: https://9lodgia.fr/domaine-de-vercasse - The cottage to a propietaire and we are on the classic card. : // 9lodgia. en / domain-of-vercasse2 For all products on the site we have nav tab. It's just for testing. We do not want to be in the design for real website. All information must be in the page without login / register page: classic, it's here: https://9lodgia.it/login and https://9lodgia.fr/register Blog homepage (https://9lodgia.fr/blog ): Classic blog page Blog post (https://9lodgia.fr/blog/urltemporaire1551521154) and static page (https://9lodgia.fr/blog/Systeme-classement-9lodgiafr): Nothing special Menu: Menu is an important part of the website. It's the way to navigate on the wbesite.
Faible participation designers
4 page

```html
<!DOCTYPE html>
<html lang="fr">
<head>
<meta charset="utf-8">
<title>9lodgia – Large Cottage Directory</title>
<link href="https://fonts.googleapis.com/css2?family=Roboto:wght@400;500;700;900&family=Open+Sans:wght@400;600;700&display=swap" rel="stylesheet">
<style>
:root{
  --blue:#0d5cf6;
  --green:#45a774;
  --mint:#7fcea6;
  --ink:#2b2b2b;
  --muted:#6f6f6f;
  --line:#dcdcdc;
  --footer:#1f1f1f;
  --white:#fff;
}
*{box-sizing:border-box;margin:0;padding:0}
html,body{width:1200px;height:3774px;overflow:hidden}
body{position:relative;background:var(--white);font-family:"Open Sans",Arial,sans-serif;color:var(--ink)}
.abs{position:absolute}
.nav{left:0;top:0;width:1200px;height:68px;background:var(--blue);color:#fff;display:flex;align-items:center;padding:0 110px;font-family:"Roboto",Arial,sans-serif}
.brand{font-size:21px;font-weight:500;margin-right:64px}
.menu{display:flex;gap:20px;font-size:14px;font-weight:500}
.menu .dd::after{content:"";display:inline-block;margin-left:6px;border:4px solid transparent;border-top-color:#fff;vertical-align:-1px}
.owner{margin-left:auto;font-size:14px;opacity:.85}
.owner::after{content:"";display:inline-block;margin-left:6px;border:4px solid transparent;border-top-color:#fff;vertical-align:-1px}
.hero{left:0;top:68px;width:1200px;height:392px;background:linear-gradient(180deg,#5b5f86 0%,#c27d8a 40%,#b46d6e 55%,#5a3b3c 75%,#2e2221 100%)}
.hero h1{position:absolute;top:120px;width:100%;text-align:center;color:#fff;font:700 44px "Roboto",Arial,sans-serif;letter-spacing:.5px}
.section-title{width:1200px;left:0;text-align:center;font:700 33px "Roboto",Arial,sans-serif;color:var(--ink)}
.cap-box{left:110px;top:644px;width:978px;height:272px;border:2px solid var(--line);border-radius:6px;display:flex;justify-content:space-between;padding:44px 12px 0}
.cap{width:150px;text-align:center}
.ring{width:140px;height:140px;margin:0 auto;border:7px solid var(--blue);border-radius:50%;display:flex;align-items:center;justify-content:center;font:700 32px "Roboto",Arial,sans-serif;color:var(--ink)}
.ring.active{border-color:var(--green)}
.cap p{margin-top:16px;font-size:15px;color:#444}
.dept{left:0;top:1021px;width:1200px;height:657px;background:var(--mint)}
.dept h2{position:absolute;top:60px;width:100%;text-align:center;color:#fff;font:700 31px "Roboto",Arial,sans-serif}
.map{position:absolute;left:335px;top:150px;width:490px;height:490px}
.arrow{width:48px;height:48px;border:2px solid #bbb;border-radius:50%;display:flex;align-items:center;justify-content:center}
.theme{top:1877px;width:232px;height:277px;border-radius:6px;overflow:hidden}
.theme span{position:absolute;bottom:18px;width:100%;text-align:center;color:#fff;font:600 20px "Open Sans",Arial,sans-serif;line-height:1.3}
.camp{left:110px;top:2264px;width:978px;height:172px;overflow:hidden}
.camp-photo{position:absolute;left:0;top:0;width:978px;height:172px;background:linear-gradient(180deg,#e7a85a 0%,#8d8f55 45%,#4f7a3a 75%,#3f6430 100%)}
.camp-text{position:absolute;left:0;top:0;height:172px}
.camp h3{position:absolute;left:36px;top:44px;color:#fff;font:700 33px "Roboto",Arial,sans-serif;white-space:nowrap}
.camp p{position:absolute;left:36px;top:96px;color:#fff;font-size:17px;white-space:nowrap}
.post{top:2727px;width:314px;height:463px;background:#fff;box-shadow:0 2px 10px rgba(0,0,0,.18)}
.post-img{height:216px}
.date{position:absolute;left:117px;top:178px;width:80px;height:80px;border-radius:50%;color:#fff;text-align:center;font:500 16px/1.2 "Roboto",Arial,sans-serif;padding-top:20px}
.date.b{background:var(--blue)}.date.g{background:var(--green)}
.post h4{position:absolute;top:278px;width:100%;text-align:center;font:600 20px "Open Sans",Arial,sans-serif;color:var(--ink)}
.post p{position:absolute;top:320px;left:30px;right:30px;text-align:center;font-size:13px;line-height:1.75;color:var(--muted)}
.post a{position:absolute;top:414px;width:100%;text-align:center;color:var(--green);font:700 13px "Open Sans",Arial,sans-serif;text-decoration:none;letter-spacing:.3px}
.footer{left:0;top:3298px;width:1200px;height:476px;background:var(--footer);color:#fff}
.footer h5{font:700 17px "Roboto",Arial,sans-serif;text-transform:uppercase;margin-bottom:30px}
.col{position:absolute;top:82px;font-size:13px}
.contact li{list-style:none;margin-bottom:24px;line-height:1.9;display:flex;gap:8px}
.contact svg{margin-top:7px;flex:none}
.links li{list-style:none;line-height:28px}
.nl p{line-height:1.9;width:360px}
.form{display:flex;margin-top:24px;width:360px;height:44px}
.form .field{flex:1;background:#fff;color:#999;display:flex;align-items:center;padding-left:26px;gap:8px;font-size:13px}
.form .btn{width:95px;background:var(--green);display:flex;align-items:center;justify-content:center;font:700 12px "Open Sans",Arial,sans-serif}
.social{display:flex;gap:10px;margin-top:28px}
.social span{width:46px;height:46px;border:2px solid #fff;border-radius:50%;display:flex;align-items:center;justify-content:center}
.social span i{width:10px;height:10px;background:#fff;border-radius:50%}
.rule{position:absolute;left:110px;top:372px;width:978px;height:1px;background:#3a3a3a}
.copy{position:absolute;top:408px;width:100%;text-align:center;font-size:13px}
</style>
</head>
<body>
<header class="abs nav">
  <div class="brand">9lodgia.Fr</div>
  <nav class="menu">
    <span class="dd">Gîte par capacité</span>
    <span class="dd">Gîte par département</span>
    <span class="dd">Gîte par thématique</span>
    <span>Blog</span>
    <span>Vos favoris</span>
  </nav>
  <div class="owner">Espace propriétaire</div>
</header>

<section class="abs hero" role="img" aria-label="Lakeside at sunset with two wicker chairs on a wooden dock">
  <h1>LARGE COTTAGE DIRECTORY</h1>
</section>

<h2 class="abs section-title" style="top:552px">LOGEMENT PAR CAPACITÉ</h2>
<div class="abs cap-box">
  <div class="cap"><div class="ring active">1 - 20</div><p>2 à 20 personnes</p></div>
  <div class="cap"><div class="ring">1 - 20</div><p>20 à 40 personnes</p></div>
  <div class="cap"><div class="ring">1 - 20</div><p>40 à 60 personnes</p></div>
  <div class="cap"><div class="ring">1 - 20</div><p>60 à 80 personnes</p></div>
  <div class="cap"><div class="ring">1 - 20</div><p>80 à 120 personnes</p></div>
  <div class="cap"><div class="ring">1 - 20</div><p>+ de 120 personnes</p></div>
</div>

<section class="abs dept">
  <h2>LOGEMENT PAR DÉPARTEMENT</h2>
  <div class="map" role="img" aria-label="Map of France divided into departments" style="background:radial-gradient(ellipse at 50% 50%,#eeeeee 0%,#eeeeee 55%,rgba(238,238,238,0) 57%)"></div>
</section>

<h2 class="abs section-title" style="top:1782px">LOGEMENT PAR THÈME</h2>
<div class="abs arrow" style="left:34px;top:1981px"><svg width="14" height="14" viewBox="0 0 14 14"><path d="M9 2L4 7l5 5" fill="none" stroke="#555" stroke-width="2"/></svg></div>
<div class="abs arrow" style="left:1121px;top:1981px"><svg width="14" height="14" viewBox="0 0 14 14"><path d="M5 2l5 5-5 5" fill="none" stroke="#555" stroke-width="2"/></svg></div>
<div class="abs theme" style="left:110px;background:linear-gradient(180deg,#c9b79b 0%,#6d604e 50%,#1f2230 100%)" role="img" aria-label="Motorcycle rider at sunset"><span>Moto classe<br>transplantée</span></div>
<div class="abs theme" style="left:360px;background:linear-gradient(180deg,#3dbcb0 0%,#1b8f8a 60%,#0f5f62 100%)" role="img" aria-label="Scuba divers underwater"><span>Aquatique</span></div>
<div class="abs theme" style="left:609px;background:linear-gradient(180deg,#c8b49a 0%,#9a6a48 55%,#4e3427 100%)" role="img" aria-label="Horse riding in the countryside"><span>Equitation</span></div>
<div class="abs theme" style="left:858px;background:linear-gradient(180deg,#8aa0b8 0%,#3d5577 50%,#142c5e 100%)" role="img" aria-label="Mountain biker on a trail"><span>vtt</span></div>

<div class="abs camp">
  <div class="camp-photo" role="img" aria-label="Tent beside a lake at sunset"></div>
  <svg class="camp-text" width="420" height="172" viewBox="0 0 420 172"><polygon points="0,0 335,0 415,172 0,172" fill="#0d5cf6"/></svg>
  <h3>Summer Camping</h3>
  <p>Nam libero temum soluta no</p>
</div>

<h2 class="abs section-title" style="top:2636px">DERNIER BLOG</h2>
<article class="abs post" style="left:110px">
  <div class="post-img" role="img" aria-label="Sailboat on the sea at sunset" style="background:linear-gradient(180deg,#9fc4de 0%,#e6c9a7 55%,#3b6f93 70%,#25506f 100%)"></div>
  <div class="date b">APR<br>10</div>
  <h4>Finibus Bonorut Malorum</h4>
  <p>Nam libero tempore, cum soluta nobis est eligendi optio cumque nihil impediquo minus id quod maxime place</p>
  <a href="#">READ MORE</a>
</article>
<article class="abs post" style="left:443px">
  <div class="post-img" role="img" aria-label="Palm trees on a beach at sunset" style="background:linear-gradient(180deg,#3f5a74 0%,#f0a957 50%,#c86b2f 72%,#2c2a26 100%)"></div>
  <div class="date g">APR<br>10</div>
  <h4>Finibus Bonorut Malorum</h4>
  <p>Nam libero tempore, cum soluta nobis est eligendi optio cumque nihil impediquo minus id quod maxime place</p>
  <a href="#">READ MORE</a>
</article>
<article class="abs post" style="left:775px">
  <div class="post-img" role="img" aria-label="Hikers crossing snowy mountains" style="background:linear-gradient(180deg,#5f9bd6 0%,#c9d6e4 45%,#f2f4f6 75%,#d7dde3 100%)"></div>
  <div class="date b">APR<br>10</div>
  <h4>Finibus Bonorut Malorum</h4>
  <p>Nam libero tempore, cum soluta nobis est eligendi optio cumque nihil impediquo minus id quod maxime place</p>
  <a href="#">READ MORE</a>
</article>

<footer class="abs footer">
  <div class="col contact" style="left:110px">
    <h5>Let's talk</h5>
    <ul>
      <li><svg width="10" height="13" viewBox="0 0 10 13"><path d="M5 0a5 5 0 0 0-5 5c0 3.5 5 8 5 8s5-4.5 5-8a5 5 0 0 0-5-5zm0 7a2 2 0 1 1 0-4 2 2 0 0 1 0 4z" fill="#fff"/></svg><span>48 Rue des Tilleuls,<br>Annecy, 74000</span></li>
      <li><svg width="12" height="12" viewBox="0 0 12 12"><path d="M2.5 0l2 3-1.2 1.5a7 7 0 0 0 4.2 4.2L9 7.5l3 2-1.5 2.5C5 12 0 7 0 1.5z" fill="#fff"/></svg><span>1 555 010 2040</span></li>
      <li><svg width="13" height="10" viewBox="0 0 13 10"><rect width="13" height="10" fill="#fff"/><path d="M0 0l6.5 5L13 0" fill="none" stroke="#1f1f1f" stroke-width="1.3"/></svg><span>info@9lodgia.fr</span></li>
    </ul>
  </div>
  <div class="col links" style="left:435px">
    <h5>Quick links</h5>
    <ul><li>Help</li><li>FAQ</li><li>Terms &amp; conditions</li><li>Return Policy</li><li>FAQ</li><li>Customer Support</li><li>Contact Us</li></ul>
  </div>
  <div class="col nl" style="left:726px">
    <h5>Newsletter subscription</h5>
    <p>Register your Email Address to get information about us</p>
    <div class="form">
      <div class="field"><svg width="13" height="10" viewBox="0 0 13 10"><rect width="13" height="10" fill="#999"/><path d="M0 0l6.5 5L13 0" fill="none" stroke="#fff" stroke-width="1.3"/></svg>Email Address</div>
      <div class="btn">SUBSCRIBE</div>
    </div>
    <div class="social"><span><i></i></span><span><i></i></span><span><i></i></span></div>
  </div>
  <div class="rule"></div>
  <div class="copy">Copyrights © 2019, 9lodgia. All Rights Reserved.</div>
</footer>
</body>
</html>
```